Bright Harbor Painters Banner

Create a banner that displays and reinforces Bright Harbor Painters’ brand identity while promoting our interior painting services. The banner will be displayed at indoor venues through the winter. The design should be clean, professional, and visually recognizable to both new and returning customers. See attached design brief & logo source files.

```html
<!DOCTYPE html>
<html lang="en">
<head>
<meta charset="utf-8">
<title>Bright Harbor Painters Banner</title>
<link rel="stylesheet" href="https://fonts.googleapis.com/css2?family=Michroma&family=Nunito:wght@800;900&family=Roboto+Condensed:wght@700&display=swap">
<style>
  :root {
    --brand-green: #6b8f52;
    --panel-charcoal: #4a4a48;
    --ink: #3b3b3b;
    --paper: #ffffff;
    --backdrop: #e9ebec;
  }
  html, body {
    margin: 0;
    padding: 0;
    width: 1200px;
    height: 879px;
    overflow: hidden;
    background: var(--backdrop);
  }
  .banner {
    position: absolute;
    left: 0;
    top: 257px;
    width: 1200px;
    height: 364px;
    background: var(--paper);
    overflow: hidden;
    box-shadow: 0 6px 24px rgba(0,0,0,0.18);
  }
  .banner-shapes {
    position: absolute;
    inset: 0;
  }
  .brand {
    position: absolute;
    left: 36px;
    top: 40px;
    display: flex;
    align-items: center;
    gap: 14px;
    color: var(--brand-green);
    font-family: "Nunito", sans-serif;
    font-weight: 900;
  }
  .brand-mark {
    width: 46px;
    height: 46px;
    background: var(--brand-green);
  }
  .brand-name {
    display: flex;
    flex-direction: column;
    line-height: 0.95;
  }
  .brand-name .first {
    font-size: 28px;
    letter-spacing: 1px;
  }
  .brand-name .second {
    font-size: 68px;
    letter-spacing: 3px;
  }
  .tagline {
    position: absolute;
    left: 0;
    top: 158px;
    width: 580px;
    margin: 0;
    text-align: center;
    font-family: "Nunito", sans-serif;
    font-weight: 800;
    font-size: 34px;
    line-height: 47px;
    color: var(--ink);
  }
  .headline {
    position: absolute;
    left: 630px;
    top: 8px;
    width: 540px;
    margin: 0;
    text-align: center;
    font-family: "Michroma", sans-serif;
    font-size: 44px;
    line-height: 53px;
    letter-spacing: 3px;
    color: var(--paper);
  }
  .services {
    position: absolute;
    left: 620px;
    top: 170px;
    width: 580px;
    margin: 0;
    padding: 0;
    list-style: none;
    text-align: center;
    font-family: "Michroma", sans-serif;
    font-size: 29px;
    line-height: 46px;
    font-weight: 700;
    color: var(--brand-green);
  }
  .cta {
    position: absolute;
    left: 18px;
    top: 310px;
    height: 54px;
    line-height: 54px;
    margin: 0;
    font-family: "Roboto Condensed", sans-serif;
    font-weight: 700;
    font-size: 31px;
    color: var(--paper);
  }
  .web {
    position: absolute;
    left: 760px;
    top: 310px;
    width: 430px;
    height: 54px;
    line-height: 54px;
    margin: 0;
    text-align: center;
    font-family: "Roboto Condensed", sans-serif;
    font-weight: 700;
    font-size: 30px;
    color: var(--paper);
  }
</style>
</head>
<body>
  <section class="banner">
    <svg class="banner-shapes" width="1200" height="364" viewBox="0 0 1200 364" aria-hidden="true">
      <polygon points="568,0 1200,0 1200,165 622,165" fill="var(--brand-green)"/>
      <polygon points="585,0 1200,0 1200,165 639,165" fill="var(--panel-charcoal)"/>
      <polygon points="0,310 700,310 735,364 0,364" fill="var(--panel-charcoal)"/>
      <polygon points="720,310 1200,310 1200,364 755,364" fill="var(--brand-green)"/>
    </svg>

    <div class="brand">
      <span class="brand-mark"></span>
      <span class="brand-name">
        <span class="first">BRIGHT HARBOR</span>
        <span class="second">PAINTERS</span>
      </span>
    </div>

    <p class="tagline">"Paint Smarter" "Trusted<br>local professionals,<br>since 2005"</p>

    <h1 class="headline">INTERIOR<br>PAINTING<br>SERVICES</h1>

    <ul class="services">
      <li>Walls · Ceilings</li>
      <li>· Trim · Cabinets</li>
      <li>· Drywall Repair</li>
    </ul>

    <p class="cta">Call to action: Book a Free Estimate at</p>
    <p class="web">www.brightharborpaint.com</p>
  </section>
</body>
</html>
```